Website for 3d printing & other services

Hi, i'm after a website to sell my 3d printed automotive parts as well as sell my 3d printing services & other services.

There's a few things i need the website to have:

- Automatic 3d print quoting based on the file the client uploads to the website.
- Shop function where i can sell my custom automotive parts
- 3D printing technologies offered are SLA & FDM
- My business can offer 3d printing, 3d scanning, 3d cad design, cnc machining, steel fabrication, drafting services.

The color design is to suit my logo which is Black, orange & white.

Target Market(s)

3d printing, automotive, fabrication

Industry/Entity Type

General manufacturing & Custom automotive parts

Coding

Coded - Design and coding required

Number of Pages Required

5+ page

Requirements
Must have
• Automatic 3d print quoting. Shop for my printed parts.

```html
<!DOCTYPE html>
<html lang="en">
<head>
<meta charset="utf-8">
<title>Forgeline Draft &amp; Design</title>
<link href="https://fonts.googleapis.com/css2?family=Russo+One&family=Roboto:wght@400;500;700&display=swap" rel="stylesheet">
<style>
:root{
  --orange:#f47b12;
  --orange-deep:#e86a0a;
  --amber:#f2a72e;
  --black:#000;
  --ink:#0b0b0b;
  --panel:#141414;
  --white:#fff;
  --muted:#cfcfcf;
}
*{box-sizing:border-box;margin:0;padding:0}
html,body{width:1200px;height:4435px;overflow:hidden}
body{background:var(--black);color:var(--white);font-family:"Roboto",Arial,sans-serif;position:relative}
.abs{position:absolute}
h2,.display{font-family:"Russo One","Arial Black",sans-serif;font-weight:400;letter-spacing:.5px}
.accent{color:var(--orange)}
.btn{position:absolute;display:inline-flex;align-items:center;gap:8px;border-radius:24px;font:700 14px "Roboto",sans-serif;text-transform:uppercase;padding:0 28px;height:40px}
.btn-orange{background:var(--orange);color:#fff}
.btn-white{background:#fff;color:var(--orange)}
.btn-white.dark{color:#111}
.dot-arrow{width:13px;height:13px;border-radius:50%;background:currentColor;position:relative}
.dot-arrow::after{content:"";position:absolute;left:3px;top:4px;border-left:6px solid #fff;border-top:3px solid transparent;border-bottom:3px solid transparent}
.btn-orange .dot-arrow::after{border-left-color:var(--orange)}
.btn-white .dot-arrow::after{border-left-color:#fff}
.photo{position:absolute}

/* header */
.site-header{position:absolute;left:0;top:0;width:1200px;height:90px;background:#000;z-index:3}
.topbar{position:absolute;left:473px;top:0;width:727px;height:27px;background:var(--orange);clip-path:polygon(0 0,100% 0,100% 100%,20px 100%);font-size:12px;font-weight:500}
.topbar span{position:absolute;top:6px}
.brand{position:absolute;left:145px;top:22px;display:flex;align-items:center;gap:8px}
.brand-mark{width:14px;height:14px;border-radius:50%;background:var(--orange)}
.brand-name{font:400 22px "Russo One",sans-serif;color:var(--orange)}
.nav{position:absolute;top:52px;left:490px;display:flex;gap:30px;font-size:14px;font-weight:700}

/* hero */
.hero{position:absolute;left:0;top:90px;width:1200px;height:745px;overflow:hidden}
.hero-title{position:absolute;left:147px;top:195px;font-size:40px}
.hero-text{position:absolute;left:147px;top:256px;width:460px;font-size:15.5px;line-height:26px;font-weight:500}

/* about */
.about-title{position:absolute;left:667px;top:878px;font-size:33px}
.body-text{font-size:13px;line-height:25px;color:#e6e6e6;text-align:justify}

/* services */
.services{position:absolute;left:0;top:1360px;width:1200px;height:560px;background:var(--ink)}
.sec-title{position:absolute;left:0;width:1200px;text-align:center;font-size:34px}
.svc-card{position:absolute;top:134px;height:348px;border-radius:12px;background:#1a1a1a;box-shadow:0 4px 10px rgba(0,0,0,.6)}
.svc-card .img{position:absolute;left:12px;top:10px;right:12px;height:262px}
.svc-card .ic{position:absolute;left:50%;top:242px;width:64px;height:64px;margin-left:-32px;border-radius:50%;background:#111}
.svc-card .label{position:absolute;left:0;right:0;top:320px;text-align:center;font-weight:700;font-size:16px}
.svc-card.active{background:var(--orange)}
.arrow-btn{position:absolute;top:1650px}

/* SLA FDM */
.tech{position:absolute;left:0;top:1920px;width:1200px;height:487px;background:linear-gradient(120deg,#2c2c2c,#1a1a1a);overflow:hidden}
.tech-icon{position:absolute;width:90px;height:90px;border-radius:50%;background:#fff}
.tech h3{position:absolute;font:400 33px "Russo One",sans-serif}

/* shop */
.product{position:absolute;top:2567px;width:253px;height:325px;background:#1a1a1a;overflow:hidden}
.product .img{position:absolute;left:0;top:0;width:100%;height:175px}
.product h4{position:absolute;left:0;right:0;top:196px;text-align:center;font-size:13px;font-weight:700}
.product p{position:absolute;left:40px;top:228px;width:180px;font-size:13px;font-weight:700;line-height:18px}
.product .corner{position:absolute;right:0;bottom:0;width:76px;height:62px;background:var(--orange);clip-path:polygon(100% 0,100% 100%,0 100%)}

/* testimonials */
.quote-box{position:absolute;top:3099px;width:393px;height:172px;border:1px solid #444;border-radius:12px;background:#111}
.quote-box p{position:absolute;left:63px;top:37px;width:305px;font-size:13px;line-height:24px;text-align:justify}
.qmark{position:absolute;font:700 44px Georgia,serif;color:var(--orange);line-height:1}
.avatar{position:absolute;top:3300px;width:68px;height:68px;border-radius:50%;border:3px solid var(--orange);background:#5b5b5b}
.person{position:absolute;top:3312px}
.person b{display:block;font-size:16px}
.person span{font-size:13px;color:#ddd}

/* contact */
.contact{position:absolute;left:0;top:3440px;width:1200px;height:700px;background:linear-gradient(#2b2f33,#111518)}
.field{position:absolute;background:#fff;color:#888;font-size:11px;padding:14px 12px}

/* footer */
.footer h5{position:absolute;top:4156px;font-size:15px;font-weight:700}
.footer ul{position:absolute;top:4195px;list-style:none;font-size:13px;line-height:24px}
.contact-item{position:absolute;left:842px;font-size:13px;line-height:19px}
.contact-item b{font-size:11px}
</style>
</head>
<body>

<header class="site-header">
  <div class="topbar"><span style="left:76px">✉ info@forgeline-design.com</span><span style="left:296px">☎ +1-555-010-2040</span><span style="left:568px">⌕</span></div>
  <div class="brand"><span class="brand-mark"></span><span class="brand-name">Forgeline</span></div>
  <nav class="nav"><span>HOME</span><span>ABOUT</span><span>OUR SERVICES</span><span>SELL</span><span>OUR CLIENTS</span><span>CONTACT</span></nav>
</header>

<section class="hero">
  <div class="photo" role="img" aria-label="Two engineers reviewing a laptop in a server room" style="inset:0;background:linear-gradient(90deg,#1c2a33 0%,#2e4452 45%,#3a5361 70%,#24323b 100%)"></div>
  <div class="photo" style="inset:0;background:linear-gradient(90deg,rgba(0,0,0,.55),rgba(0,0,0,0) 60%)"></div>
  <h1 class="hero-title display">FORGELINE DRAFT AND DESIGN</h1>
  <p class="hero-text">Lorem ipsum dolor sit amet, consectetur adipiscing elit, sed do tempor incididunt ut labore et magna aliqua.</p>
  <span class="btn btn-orange" style="left:147px;top:333px;height:46px">Get Started <span class="dot-arrow" style="background:#fff"></span></span>
  <svg class="abs" style="left:0;top:570px" width="1200" height="175" viewBox="0 0 1200 175">
    <polygon points="0,0 1200,0 1200,175 0,175" fill="none"/>
    <polygon points="0,140 0,175 1200,175 1200,150" fill="#000"/>
    <polygon points="0,140 460,5 720,105 300,60 0,175" fill="#f47b12"/>
    <polygon points="300,60 720,105 460,5" fill="#e8711a"/>
    <polygon points="560,110 1000,55 1200,80 1200,110 850,150" fill="#f2a72e"/>
    <polygon points="1000,55 1200,20 1200,80" fill="#f47b12"/>
    <polygon points="0,175 300,60 720,105 850,150 1200,110 1200,175" fill="#000"/>
  </svg>
</section>

<section class="about">
  <div class="abs" style="left:124px;top:1004px;width:310px;height:279px;border:9px solid var(--orange);border-top:none;border-right:none"></div>
  <div class="abs" style="left:124px;top:1004px;width:12px;height:279px;background:var(--orange)"></div>
  <div class="abs" style="left:124px;top:1274px;width:310px;height:10px;background:var(--orange)"></div>
  <div class="photo" role="img" aria-label="Smiling engineer with arms crossed in a 3D printing workshop" style="left:139px;top:852px;width:441px;height:417px;background:linear-gradient(135deg,#d9dde2,#8a97a6 55%,#2e4c78)"></div>
  <h2 class="about-title">ABOUT <span class="accent">US</span></h2>
  <p class="abs body-text" style="left:667px;top:935px;width:386px">Lorem ipsum dolor sit amet, consectetur adipiscing elit, sed do eiusmod tempor incididunt ut labore et dolore magna aliqua. Ut enim ad minim veniam, quis nostrud exercitation ullamco laboris nisi ut aliquip ex ea commodo consequat.</p>
  <p class="abs body-text" style="left:667px;top:1045px;width:386px">Duis aute irure dolor in reprehenderit in voluptate velit esse cillum dolore eu fugiat nulla pariatur. Excepteur sint occaecat cupidatat non proident, sunt in culpa qui officia deserunt mollit anim id est laborum.Unde omnis iste natus error sit voluptatem accusantium doloremque laudantium, totam rem aperiam.</p>
  <span class="btn btn-orange" style="left:667px;top:1198px">Read More <span class="dot-arrow" style="background:#fff"></span></span>
</section>

<section class="services">
  <h2 class="sec-title" style="top:60px"><span class="accent">OUR</span> SERVICES</h2>
  <div class="svc-card" style="left:141px;width:293px">
    <div class="img" role="img" aria-label="Laser nozzle of a 3D printer with sparks" style="background:linear-gradient(160deg,#9fc3ea,#3a6fb5 60%,#1d3f78)"></div>
    <div class="ic"><svg width="64" height="64"><circle cx="32" cy="32" r="16" fill="none" stroke="#f47b12" stroke-width="2"/><rect x="24" y="28" width="16" height="10" fill="none" stroke="#f47b12" stroke-width="2"/></svg></div>
    <div class="label">3D Printing</div>
  </div>
  <div class="svc-card active" style="left:455px;width:289px">
    <div class="abs" style="left:103px;top:28px;width:84px;height:84px;border-radius:50%;background:#fff"><svg width="84" height="84"><path d="M32 30h20l-4 10H36z M42 40v14 M34 56h16" fill="none" stroke="#f47b12" stroke-width="2.5"/></svg></div>
    <div class="abs" style="left:0;right:0;top:134px;text-align:center;font-weight:700;font-size:16px">3D Scanning</div>
    <p class="abs" style="left:28px;right:28px;top:162px;text-align:center;font-size:13px;line-height:23px">Lorem ipsum dolor amet, consectetur adipiscing elit, sed do eiusmod tempor labore dolore magna aliqua Ut enim ad minim veniam.</p>
    <span class="btn btn-white" style="left:70px;top:272px;height:36px;padding:0 24px">Learn More <span class="dot-arrow"></span></span>
    <svg class="abs" style="left:16px;top:0" width="20" height="16"><polygon points="0,0 20,0 10,14" fill="#fff"/></svg>
    <svg class="abs" style="right:16px;bottom:0" width="20" height="16"><polygon points="10,2 20,16 0,16" fill="#fff"/></svg>
  </div>
  <div class="svc-card" style="left:764px;width:293px">
    <div class="img" role="img" aria-label="CNC machine cutting metal with sparks" style="background:linear-gradient(160deg,#3b4a5a,#6e7781 45%,#c86a1e 75%,#2b2f35)"></div>
    <div class="ic"><svg width="64" height="64"><circle cx="32" cy="32" r="14" fill="none" stroke="#f47b12" stroke-width="2" stroke-dasharray="5 3"/><circle cx="32" cy="32" r="5" fill="none" stroke="#f47b12" stroke-width="2"/></svg></div>
    <div class="label">CNC Machining</div>
  </div>
</section>
<svg class="arrow-btn" style="left:42px" width="52" height="30"><line x1="0" y1="15" x2="52" y2="15" stroke="#f47b12" stroke-width="2"/><polyline points="26,2 13,15 26,28" fill="none" stroke="#f47b12" stroke-width="2"/></svg>
<svg class="arrow-btn" style="left:1106px" width="52" height="30"><line x1="0" y1="15" x2="52" y2="15" stroke="#f47b12" stroke-width="2"/><polyline points="26,2 39,15 26,28" fill="none" stroke="#f47b12" stroke-width="2"/></svg>

<section class="tech">
  <div class="abs" role="img" aria-label="Faint machinery background" style="inset:0;background:linear-gradient(90deg,#303030,#242424)"></div>
  <svg class="abs" style="left:0;top:0" width="1200" height="487"><polygon points="637,0 1200,0 1200,487 542,487" fill="#f47b12"/></svg>
  <div class="tech-icon" style="left:144px;top:55px"><svg width="90" height="90"><rect x="27" y="22" width="34" height="44" fill="none" stroke="#222" stroke-width="2"/><text x="31" y="50" font-family="Roboto" font-size="13" fill="#222">SLA</text></svg></div>
  <h3 style="left:262px;top:80px">SLA</h3>
  <p class="abs body-text" style="left:143px;top:164px;width:390px;color:#fff">Lorem ipsum dolor sit amet, consectetur adipiscing elit, sed do eiusmod tempor incididunt ut labore et dolore magna aliqua. Ut enim ad minim veniam, quis nostrud exercitation ullamco laboris nisi ut aliquip ex ea commodo consequat. Duis aute irure dolor in reprehenderit in voluptate velit esse cillum dolore eu fugiat nulla pariatur. Excepteur sint occaecat cupidatat.</p>
  <p class="abs body-text" style="left:143px;top:320px;width:390px;color:#fff">Sed ut perspiciatis unde omnis iste natus error sit voluptatem accusantium doloremque laudantium, totam rem.</p>
  <span class="btn btn-white dark" style="left:144px;top:395px">Read More <span class="dot-arrow"></span></span>
  <div class="tech-icon" style="left:669px;top:55px"><svg width="90" height="90"><rect x="28" y="26" width="28" height="36" fill="none" stroke="#f47b12" stroke-width="2"/><rect x="34" y="20" width="28" height="36" fill="#fff" stroke="#f47b12" stroke-width="2"/><circle cx="48" cy="38" r="7" fill="none" stroke="#f47b12" stroke-width="2"/></svg></div>
  <h3 style="left:787px;top:80px">FDM</h3>
  <p class="abs body-text" style="left:668px;top:164px;width:390px;color:#fff">Lorem ipsum dolor sit amet, consectetur adipiscing elit, sed do eiusmod tempor incididunt ut labore et dolore magna aliqua. Ut enim ad minim veniam, quis nostrud exercitation ullamco laboris nisi ut aliquip ex ea commodo consequat. Duis aute irure dolor in reprehenderit in voluptate velit esse cillum dolore eu fugiat nulla pariatur. Excepteur sint occaecat cupidatat.</p>
  <p class="abs body-text" style="left:668px;top:320px;width:390px;color:#fff">Sed ut perspiciatis unde omnis iste natus error sit voluptatem accusantium doloremque laudantium, totam rem.</p>
  <span class="btn btn-white" style="left:669px;top:395px">Read More <span class="dot-arrow"></span></span>
</section>

<section class="shop">
  <h2 class="sec-title" style="top:2482px">SHOP MY <span class="accent">CUSTOM</span> AUTOMOTIVE <span class="accent">PARTS</span></h2>
  <svg class="abs" style="left:76px;top:2710px" width="24" height="44"><polyline points="20,2 4,22 20,42" fill="none" stroke="#555" stroke-width="3"/></svg>
  <svg class="abs" style="left:1100px;top:2710px" width="24" height="44"><polyline points="4,2 20,22 4,42" fill="none" stroke="#555" stroke-width="3"/></svg>
  <div class="product" style="left:177px">
    <div class="img" role="img" aria-label="Machined metal shaft part" style="background:radial-gradient(circle at 50% 70%,#a33,#3b3b3b 55%,#151515)"></div>
    <h4>PRODUCT 01</h4><p>lorem ipsum dolor sit amet consectuer adipiscing</p><div class="corner"></div>
  </div>
  <div class="product" style="left:473px">
    <div class="img" role="img" aria-label="Engine gears with glowing orange highlights" style="background:radial-gradient(circle at 55% 55%,#e5561c,#4a4f57 45%,#1a1c20)"></div>
    <h4>PRODUCT 02</h4><p>lorem ipsum dolor sit amet consectuer adipiscing</p><div class="corner"></div>
  </div>
  <div class="product" style="left:770px">
    <div class="img" role="img" aria-label="Row of shock absorber parts" style="background:linear-gradient(120deg,#1c1c1c,#8d9096 40%,#b33 60%,#2a2a2a)"></div>
    <h4>PRODUCT 03</h4><p>lorem ipsum dolor sit amet consectuer adipiscing</p><div class="corner"></div>
  </div>
</section>

<section class="testimonials">
  <h2 class="sec-title" style="top:3020px">WHAT OUR <span class="accent">CLIENT</span> SAYS</h2>
  <div class="quote-box" style="left:182px">
    <span class="qmark" style="left:20px;top:18px">“</span>
    <p>Lorem ipsum dolor sit amet, consectetur adipiscing elit, sed do eiusmod tempor incididunt ut labore et dolore magna aliqua. Ut enim ad minim veniam. quis nostrud exercitation ullamco.</p>
    <span class="qmark" style="left:336px;top:98px">”</span>
  </div>
  <svg class="abs" style="left:212px;top:3270px" width="30" height="16"><polygon points="0,0 30,0 15,15" fill="#111" stroke="#444"/></svg>
  <div class="avatar" style="left:185px" role="img" aria-label="Client portrait"></div>
  <div class="person" style="left:272px"><b>Maren</b><span>Lorem ipsum dolor</span></div>
  <div class="quote-box" style="left:623px">
    <span class="qmark" style="left:18px;top:18px">“</span>
    <p style="left:64px">Lorem ipsum dolor sit amet, consectetur adipiscing elit, sed do eiusmod tempor incididunt ut labore et dolore magna aliqua. Ut enim ad minim veniam, quis nostrud exercitation ullamco.</p>
    <span class="qmark" style="left:336px;top:104px">”</span>
  </div>
  <svg class="abs" style="left:653px;top:3270px" width="30" height="16"><polygon points="0,0 30,0 15,15" fill="#111" stroke="#444"/></svg>
  <div class="avatar" style="left:626px" role="img" aria-label="Client portrait"></div>
  <div class="person" style="left:714px"><b>Theo Lark</b><span>Lorem ipsum dolor</span></div>
</section>

<section class="contact">
  <div class="abs" role="img" aria-label="City skyline at dusk" style="inset:0;background:linear-gradient(#2e3236,#1b1f22 70%,#0e0f10)"></div>
  <h2 class="sec-title" style="top:68px">CONTACT <span class="accent">US</span></h2>
  <p class="abs" style="left:320px;width:560px;top:126px;text-align:center;font-size:13px;line-height:24px">Lorem ipsum dolor sit amet, consectetur adipiscing elit, sed do eiusmod tempor incididunt ut labore et dolore magna aliqua. Ut enim ad minim veniam,</p>
  <div class="field" style="left:241px;top:198px;width:353px;height:41px">👤 First Name</div>
  <div class="field" style="left:604px;top:198px;width:355px;height:41px">👤 Last Name</div>
  <div class="field" style="left:241px;top:253px;width:353px;height:40px">✉ Email Address</div>
  <div class="field" style="left:604px;top:253px;width:355px;height:40px">☎ Phone Number</div>
  <div class="field" style="left:241px;top:306px;width:718px;height:88px">✎ Message</div>
  <span class="btn btn-white" style="left:525px;top:433px;height:38px;padding:0 24px">Get A Quote <span class="dot-arrow"></span></span>
  <svg class="abs" style="left:0;top:580px" width="1200" height="120"><polygon points="0,40 640,0 360,95 0,85" fill="#f2a72e"/><polygon points="360,95 640,0 1050,40 1200,15 1200,70 760,85" fill="#f47b12"/><polygon points="0,85 360,95 760,85 1200,70 1200,120 0,120" fill="#000"/><polygon points="0,65 280,50 0,88" fill="#f47b12"/></svg>
</section>

<footer class="footer">
  <div class="abs" style="left:145px;top:4185px;display:flex;align-items:center;gap:10px"><span class="brand-mark" style="width:20px;height:20px"></span><span class="brand-name" style="font-size:38px">Forgeline</span></div>
  <div class="abs" style="left:145px;top:4245px;font:400 19px 'Russo One',sans-serif">DRAFT &amp; DESIGN</div>
  <div class="abs" style="left:186px;top:4305px;display:flex;gap:14px"><span style="width:14px;height:14px;border-radius:50%;background:#fff"></span><span style="width:14px;height:14px;border-radius:50%;background:#fff"></span><span style="width:14px;height:14px;border-radius:50%;background:#fff"></span><span style="width:14px;height:14px;border-radius:50%;background:#fff"></span></div>
  <h5 style="left:427px">Quick Links</h5>
  <ul style="left:427px"><li>Home</li><li>About</li><li>Our Services</li><li>Sell</li><li>Our Clients</li><li>Contact</li></ul>
  <h5 style="left:599px">About Company</h5>
  <ul style="left:599px"><li>Legal Information</li><li>Terms &amp; Condition</li><li>Privacy Policy</li><li>Support</li><li>Site Map</li><li>FAQ</li></ul>
  <h5 style="left:821px">Contact Us</h5>
  <span class="abs accent" style="left:818px;top:4195px">☎</span>
  <div class="contact-item" style="top:4195px"><b>Phone</b><br>+1 555 010 2040</div>
  <span class="abs accent" style="left:818px;top:4242px">✉</span>
  <div class="contact-item" style="top:4242px"><b>Email</b><br>info@forgeline-design.com</div>
  <span class="abs accent" style="left:818px;top:4291px">●</span>
  <div class="contact-item" style="top:4291px;width:230px"><b>Location</b><br>24 Lorem ipsum dolor sit consectetur adipiscing elit,</div>
  <div class="abs" style="left:1080px;top:4305px;width:34px;height:34px;border-radius:50%;background:var(--orange)"><svg width="34" height="34"><polyline points="11,20 17,13 23,20" fill="none" stroke="#fff" stroke-width="2.5"/></svg></div>
  <div class="abs" style="left:145px;top:4384px;width:910px;height:1px;background:#333"></div>
  <p class="abs" style="left:0;width:1200px;top:4398px;text-align:center;font-size:11px;color:#ddd">2023 Copyright - Forgeline Draft&amp;Design &nbsp;|&nbsp; All Rights Reserved</p>
</footer>

</body>
</html>
```